To design a brand identity that is simple and creative with 'Corvane' as the brand name, I like modern simple fonts like helvetica neue, I want to print both sides of the card, I am open to dark front and white back, but the design needs to transfer well to letter heads and email signatures, I am looking for sophisticated and elegant, but open minded about clever and off the wall, I do not do 'boring' Corvane Ventures is the mother company for a small group, specialising in Management & consulting, Software development and construction, we have a high level of integrity, we are transparent and accountable for what we do. my images are provided as a guide only, Im not expecting them to be just copied, Im looking for a creator and passionate thinker, who will put life into their work.

Target Market(s)

usually business minded people who are looking for something different in me, such as leadership, confidence and focus with thinking that is per haps a little outside the box..

Industry/Entity Type

Construction

Requirements
Must have
• clean, minmalistic
Nice to have
• custom logo
Should not have
• boring, traditional

```html
<!DOCTYPE html>
<html lang="en">
<head>
<meta charset="utf-8">
<title>Corvane – Business Card</title>
<link rel="stylesheet" href="https://fonts.googleapis.com/css2?family=Raleway:wght@400;700&display=swap">
<style>
  :root {
    --canvas: #ece7e1;
    --card-dark: #1d1d20;
    --card-light: #ffffff;
    --accent-magenta: #c2255c;
    --name-yellow: #f3b51b;
    --text-white: #ffffff;
    --tagline-grey: #9a9a9a;
    --service-coral: #ee4e4b;
    --bullet-grey: #9a9a9a;
    --web-ink: #2f2f2f;
  }
  * { margin: 0; padding: 0; box-sizing: border-box; }
  html, body {
    width: 1200px;
    height: 720px;
    overflow: hidden;
    background: var(--canvas);
    font-family: "Raleway", "Helvetica Neue", Arial, sans-serif;
  }
  .stage {
    width: 1200px;
    height: 720px;
    display: flex;
    align-items: center;
    justify-content: center;
    gap: 40px;
  }
  .card {
    position: relative;
    width: 540px;
    height: 309px;
    border-radius: 4px;
    overflow: hidden;
    box-shadow: 0 6px 18px rgba(0, 0, 0, 0.18);
  }
  .card--front { background: var(--card-dark); }
  .card--back { background: var(--card-light); }

  .brand-mark {
    position: absolute;
    border-radius: 50%;
    background: var(--accent-magenta);
  }
  .brand-name {
    position: absolute;
    font-weight: 400;
    line-height: 1;
    text-transform: uppercase;
  }

  /* Front */
  .color-band {
    position: absolute;
    left: 0;
    right: 0;
    bottom: 0;
    height: 44px;
    background: linear-gradient(90deg, #f7a21b 0%, #ee2a24 30%, #c21f4f 55%, #8a3b7a 75%, #1fa08f 100%);
  }
  .card--front .brand-mark { left: 34px; top: 96px; width: 44px; height: 44px; }
  .card--front .brand-name {
    left: 92px;
    top: 98px;
    font-size: 40px;
    letter-spacing: 6px;
    color: var(--text-white);
  }
  .tagline {
    position: absolute;
    left: 94px;
    top: 148px;
    font-size: 13px;
    letter-spacing: 1px;
    color: var(--tagline-grey);
  }
  .holder {
    position: absolute;
    left: 34px;
    top: 206px;
    color: var(--text-white);
  }
  .holder-name {
    font-weight: 700;
    font-size: 16px;
    color: var(--name-yellow);
  }
  .holder-title { font-size: 13px; margin-top: 2px; }
  .contact-list {
    position: absolute;
    right: 24px;
    top: 186px;
    list-style: none;
    color: var(--text-white);
    font-size: 12px;
  }
  .contact-list li {
    height: 22px;
    display: flex;
    align-items: center;
    justify-content: flex-end;
    gap: 6px;
  }
  .contact-icon { width: 11px; height: 11px; flex: none; }

  /* Back */
  .card--back .brand-mark { left: 44px; top: 106px; width: 58px; height: 58px; }
  .card--back .brand-name {
    left: 122px;
    top: 108px;
    font-size: 56px;
    letter-spacing: 8px;
    color: var(--web-ink);
  }
  .services {
    position: absolute;
    left: 60px;
    top: 194px;
    color: var(--service-coral);
    font-size: 15px;
    line-height: 1.45;
  }
  .services .bullet { color: var(--bullet-grey); margin: 0 3px 0 6px; }
  .services .line-2 { padding-left: 150px; }
  .website {
    position: absolute;
    left: 0;
    right: 0;
    top: 254px;
    text-align: center;
    font-size: 15px;
    letter-spacing: 4px;
    color: var(--web-ink);
  }
</style>
</head>
<body>
<main class="stage">

  <section class="card card--front" aria-label="Business card front">
    <div class="color-band" role="img" aria-label="Warm-to-teal colour band decoration"></div>

    <span class="brand-mark" aria-hidden="true"></span>
    <span class="brand-name">Corvane</span>
    <span class="tagline">in the creation business</span>

    <div class="holder">
      <div class="holder-name">Your Name</div>
      <div class="holder-title">Title</div>
    </div>

    <ul class="contact-list">
      <li>
        <svg class="contact-icon" viewBox="0 0 12 12" aria-hidden="true">
          <circle cx="6" cy="6" r="5.5" fill="var(--name-yellow)"/>
          <path d="M4 3.2 L5.2 3 L5.8 4.6 L5 5.2 Q5.6 6.6 6.9 7.1 L7.5 6.3 L9 6.9 L8.8 8.1 Q5 8.5 3.9 4.3 Z" fill="#1d1d20"/>
        </svg>
        +61 0400 517 294
      </li>
      <li>
        <svg class="contact-icon" viewBox="0 0 12 12" aria-hidden="true">
          <rect x="0.5" y="2.5" width="11" height="7" rx="1" fill="var(--name-yellow)"/>
          <path d="M0.8 3 L6 6.8 L11.2 3" fill="none" stroke="#1d1d20" stroke-width="1"/>
        </svg>
        names@corvane.ventures
      </li>
      <li>Po Box 418 Perth 6000</li>
    </ul>
  </section>

  <section class="card card--back" aria-label="Business card back">
    <span class="brand-mark" aria-hidden="true"></span>
    <span class="brand-name">Corvane</span>

    <div class="services">
      <div class="line-1"><span class="bullet">•</span>Management &amp; Consulting <span class="bullet">•</span>Software Development</div>
      <div class="line-2"><span class="bullet">•</span>Construction</div>
    </div>

    <div class="website">www.corvane.com</div>
  </section>

</main>
</body>
</html>
```